Harbourline Electrical Solutions

On one side. LOGO (underneath:) Commercial Industrial Residential

- NAME & CONTACT DETAILS

Marcus T. Hollings
Project Manager

(Cell icon) (441) 555-0187
(Email icon) hlelectricalsolutions@mailvento.com
(Facebook & Instagram icons )@hlelectricalsolutions

Other side: LOGO - underneath ELECTRICAL CONSTRUCTION & MAINTENANCE . LED LIGHTING & AUTOMATION . LIFE SAFETY SYSTEMS (FIRE ALARM / SECURITY) . DATA & COMMUNICATION

```html
<!DOCTYPE html>
<html lang="en">
<head>
<meta charset="utf-8">
<title>Harbourline Electrical Solutions – Business Card</title>
<link rel="stylesheet" href="https://fonts.googleapis.com/css2?family=Montserrat:wght@400;500;600&family=Oswald:wght@600&display=swap">
<style>
  :root {
    --backdrop: #d9d9d9;
    --card-dark: #565656;
    --card-dark-text: #2f2f2f;
    --card-dark-light: #cfcfcf;
    --paper: #ffffff;
    --teal: #1a6475;
    --teal-light: #1f8196;
    --ink: #3a3a3a;
    --divider: #7a7a7a;
  }
  * { box-sizing: border-box; margin: 0; padding: 0; }
  html, body { width: 1200px; height: 960px; overflow: hidden; }
  body {
    background: var(--backdrop);
    font-family: "Montserrat", Arial, sans-serif;
    display: flex; flex-direction: column; align-items: center; justify-content: center;
    gap: 40px;
  }
  .card {
    width: 760px; height: 420px; position: relative; overflow: hidden;
    box-shadow: 0 6px 18px rgba(0,0,0,.18);
  }

  /* Back side */
  .card--back { background: var(--card-dark); display: flex; flex-direction: column; align-items: center; justify-content: center; gap: 50px; }
  .brand { display: flex; align-items: center; gap: 22px; }
  .brand__square { width: 20px; height: 20px; }
  .brand__name { font-weight: 500; letter-spacing: 4px; line-height: 1.15; text-transform: uppercase; font-size: 26px; }
  .card--back .brand__square { background: var(--card-dark-text); }
  .card--back .brand__name { color: var(--card-dark-text); }
  .services { text-align: center; color: var(--card-dark-light); font-size: 14px; line-height: 1.8; letter-spacing: .3px; }
  .services .dot { color: var(--card-dark-text); margin: 0 6px; }

  /* Front side */
  .card--front { background: var(--paper); }
  .front__top { height: 248px; display: flex; flex-direction: column; align-items: center; justify-content: center; gap: 22px; }
  .card--front .brand__square { background: var(--teal); }
  .card--front .brand__name { color: var(--teal); font-size: 24px; }
  .sectors { color: var(--ink); font-size: 15px; letter-spacing: 1.5px; text-transform: uppercase; }
  .sectors .dot { margin: 0 8px; }
  .front__rule { height: 10px; background: linear-gradient(#8a8a8a, #5e5e5e); }
  .front__band {
    height: 162px; background: linear-gradient(100deg, var(--teal), var(--teal-light));
    display: flex; align-items: center; justify-content: space-between; padding: 0 56px 0 60px; color: #fff;
  }
  .person__name { font-family: "Oswald", "Arial Narrow", sans-serif; font-weight: 600; font-size: 38px; letter-spacing: 1px; text-transform: uppercase; line-height: 1.05; }
  .person__role { font-size: 17px; margin-top: 2px; padding-left: 120px; }
  .contacts { list-style: none; font-size: 15px; line-height: 1.65; }
  .contacts li { display: flex; align-items: center; gap: 10px; }
  .contacts svg { width: 16px; height: 16px; flex: none; }
  .social-dot { width: 14px; height: 14px; border-radius: 50%; background: #fff; flex: none; margin: 0 1px; }
</style>
</head>
<body>

  <section class="card card--back" aria-label="Card back">
    <div class="brand">
      <span class="brand__square"></span>
      <p class="brand__name">Harbourline<br>Electrical<br>Solutions</p>
    </div>
    <p class="services">
      Electrical Construction &amp; Maintenance<span class="dot">•</span>LED Lighting &amp; Automation<br>
      Life Safety Systems (Fire Alarm / Security)<span class="dot">•</span>Data &amp; Communication
    </p>
  </section>

  <section class="card card--front" aria-label="Card front">
    <div class="front__top">
      <div class="brand">
        <span class="brand__square"></span>
        <p class="brand__name">Harbourline<br>Electrical<br>Solutions</p>
      </div>
      <p class="sectors">Commercial<span class="dot">•</span>Industrial<span class="dot">•</span>Residential</p>
    </div>
    <div class="front__rule"></div>
    <div class="front__band">
      <div class="person">
        <p class="person__name">Marcus T. Hollings</p>
        <p class="person__role">Project Manager</p>
      </div>
      <ul class="contacts">
        <li>
          <svg viewBox="0 0 16 16" aria-hidden="true"><rect x="4" y="1" width="8" height="14" rx="1.5" fill="none" stroke="#fff" stroke-width="1.4"/><circle cx="8" cy="12.5" r=".9" fill="#fff"/></svg>
          (441) 555-0187
        </li>
        <li>
          <svg viewBox="0 0 16 16" aria-hidden="true"><rect x="1" y="3.5" width="14" height="9" fill="#fff"/><path d="M1 3.5 8 9l7-5.5" fill="none" stroke="#1a6475" stroke-width="1.2"/></svg>
          hlelectricalsolutions@mailvento.com
        </li>
        <li><span class="social-dot"></span>@hlelectricalsolutions</li>
        <li><span class="social-dot"></span>@hlelectricalsolutions</li>
      </ul>
    </div>
  </section>

</body>
</html>
```